Need business card with a logo for a hearing aid sales and audiology business. We have two Hearing Instrument Specialists and one Audiologist on staff. Over 25 years in business. Locally owned and operated. Financing available. Most insurances accepted.

Summit Audio Wellness LLC
48730 W Larchmont, Suite 7
Spokane, WA 99281
509-617-2084
www.summitaudiowell.example

Manager
Tobias Kerrell HIS COHC
License #71829046

Target Market(s)

50yr old + people with a hearing loss.

Industry/Entity Type

Business

Contact Information for Business Card

48730 W Larchmont, Suite 7
Spokane, WA 99281
509-617-2084
www.summitaudiowell.example

Manager
Tobias Kerrell HIS COHC
NLVE #71829046

Font styles to use
Serif
Sans Serif

Requirements
Must have
• Business name, Tobias's name and title(s) and contact information, License #, web address

```html
<!DOCTYPE html>
<html lang="en">
<head>
<meta charset="utf-8">
<title>Summit Audio Wellness – Business Card</title>
<link rel="stylesheet" href="https://fonts.googleapis.com/css2?family=Cinzel:wght@500&family=Josefin+Sans:wght@300;400&display=swap">
<style>
  :root {
    --stage: #bdbdbd;
    --card: #1f1e1f;
    --green: #8cc63f;
    --silver: #cfcfcf;
    --text: #e6e6e6;
  }
  * { margin: 0; padding: 0; box-sizing: border-box; }
  html, body {
    width: 1200px; height: 800px; overflow: hidden;
    background: var(--stage);
  }
  .canvas {
    width: 1200px; height: 800px;
    display: flex; align-items: center; justify-content: center;
  }
  .card {
    position: relative;
    width: 1050px; height: 600px;
    background: var(--card);
    border-radius: 44px;
    font-family: "Josefin Sans", sans-serif;
    font-weight: 300;
    color: var(--text);
  }
  .brand {
    position: absolute; left: 110px; top: 110px;
    display: flex; align-items: center; gap: 30px;
  }
  .brand__dot {
    width: 84px; height: 84px; border-radius: 50%;
    background: var(--green);
  }
  .brand__name {
    font-family: "Cinzel", serif; font-weight: 500;
    font-size: 46px; letter-spacing: 4px;
    color: var(--silver);
    line-height: 1;
  }
  .contact {
    position: absolute; left: 600px; top: 290px;
    font-size: 26px; line-height: 1.3;
  }
  .contact__row { display: flex; align-items: flex-start; gap: 12px; }
  .contact__row + .contact__row { margin-top: 6px; }
  .contact__icon { width: 26px; height: 26px; flex: none; margin-top: 1px; }
  .contact__row--address .contact__icon { margin-top: 36px; }
  .person {
    position: absolute; left: 140px; top: 380px; width: 330px;
  }
  .person__name {
    font-size: 34px; color: var(--green); font-weight: 400;
  }
  .person__creds { font-size: 20px; color: var(--text); margin-left: 6px; }
  .person__rule { height: 2px; background: var(--green); opacity: .8; }
  .person__title { font-size: 24px; padding: 6px 0 10px 12px; }
  .person__license { font-size: 24px; padding: 12px 0 0 24px; }
  .website {
    position: absolute; left: 0; right: 0; bottom: 50px;
    text-align: center; font-size: 30px;
  }
  .website__domain { color: var(--green); }
</style>
</head>
<body>
<main class="canvas">
  <section class="card" aria-label="Summit Audio Wellness business card">
    <header class="brand">
      <span class="brand__dot" aria-hidden="true"></span>
      <h1 class="brand__name">SUMMIT AUDIO WELLNESS</h1>
    </header>

    <div class="person">
      <p class="person__name">Tobias Kerrell<span class="person__creds">HIS COHC</span></p>
      <div class="person__rule"></div>
      <p class="person__title">Manager</p>
      <div class="person__rule"></div>
      <p class="person__license">NLVE #71829046</p>
    </div>

    <address class="contact" style="font-style:normal">
      <div class="contact__row">
        <svg class="contact__icon" viewBox="0 0 26 26" aria-hidden="true">
          <circle cx="13" cy="13" r="11.5" fill="none" stroke="var(--green)" stroke-width="2"/>
          <path d="M9 7.5c-1 .8-1.6 2-1 3.6 1.2 3 3.6 5.5 6.6 6.8 1.6.6 2.8 0 3.6-1l-2.2-2.1-1.6 1c-1.6-.8-2.9-2.1-3.7-3.7l1-1.6z" fill="var(--green)"/>
        </svg>
        <span>509-617-2084</span>
      </div>
      <div class="contact__row contact__row--address">
        <svg class="contact__icon" viewBox="0 0 26 26" aria-hidden="true">
          <circle cx="13" cy="13" r="11.5" fill="var(--green)"/>
          <ellipse cx="13" cy="13" rx="5" ry="11.5" fill="none" stroke="var(--card)" stroke-width="1.5"/>
          <line x1="1.5" y1="13" x2="24.5" y2="13" stroke="var(--card)" stroke-width="1.5"/>
        </svg>
        <span>48730 W Larchmont, Suite 7<br>Spokane, WA 99281</span>
      </div>
    </address>

    <p class="website">www.<span class="website__domain">summitaudiowell</span>.example</p>
  </section>
</main>
</body>
</html>
```